Financial cloud based software needs a print design for a trade show booth

We have a cloud based system that captures, values and reports financial instruments. Our client base is medium sized corporates who use derivatives for hedging their financial exposures. We are showcasing our software at a conference and need a design that can be printed and used on our booth. The print size will be 2176mm(w) x 915mm (h). The conference is aimed at accountants. The design must incorporate the following bullet points:

• CVA/DVA (AASB 13 compliant)
• Independent valuations
• FX, interest rates and commodities
• Low monthly subscription

The design also needs to incorporate the attached Wren's Ledger and Fenlaris logos. I have also attached a word doc that gives a basic layout. I'd also like to use the Fenlaris "blue" as the background colour which goes from:
CMYK: 50, 0, 0, 0, RGB: 108, 206, 245 to
CMYK: 85, 50, 0, 0, RGB: 27,117,186
I have attached the brand guide fyi.
It would be good to incorporate the website address in the design somewhere too (www.fenlarispro-example.com).

```html
<!DOCTYPE html>
<html lang="en">
<head>
<meta charset="utf-8">
<title>Fenlaris – Trade Show Banner</title>
<link rel="stylesheet" href="https://fonts.googleapis.com/css2?family=Inter:wght@700&display=swap">
<style>
  :root {
    --blue-deep: #1b75ba;
    --blue-light: #6ccef5;
    --ink: #231f20;
    --white: #ffffff;
    --navy: #2b2d6e;
    --aqua: #3fa9e0;
    --graphite: #3a3a3a;
  }
  * { margin: 0; padding: 0; box-sizing: border-box; }
  html, body {
    width: 1200px;
    height: 506px;
    overflow: hidden;
    background: var(--white);
  }
  .banner {
    position: relative;
    width: 1200px;
    height: 506px;
    font-family: "Inter", "Helvetica Neue", Arial, sans-serif;
    font-weight: 700;
  }
  .feature-band {
    position: absolute;
    inset: 0 0 auto 0;
    height: 336px;
    background: linear-gradient(90deg, var(--blue-deep) 0%, #3f9ad6 55%, var(--blue-light) 100%);
    padding: 14px 0 0 22px;
  }
  .feature-list { list-style: none; }
  .feature {
    display: flex;
    align-items: center;
    height: 59px;
    font-size: 52px;
    letter-spacing: -0.5px;
    color: var(--ink);
    white-space: nowrap;
  }
  .feature-marker {
    flex: none;
    width: 36px;
    height: 36px;
    margin-right: 22px;
  }
  .brand-row {
    position: absolute;
    left: 0;
    right: 0;
    top: 336px;
    height: 170px;
    display: flex;
    align-items: center;
    justify-content: space-between;
    padding: 0 30px 0 32px;
  }
  .brand {
    display: flex;
    align-items: center;
    gap: 16px;
    font-size: 50px;
    letter-spacing: -0.5px;
  }
  .brand-dot { width: 46px; height: 46px; flex: none; }
  .brand--partner { color: var(--navy); }
  .brand--product { color: var(--graphite); }
</style>
</head>
<body>
  <main class="banner">
    <section class="feature-band">
      <ul class="feature-list">
        <li class="feature"><svg class="feature-marker" viewBox="0 0 36 36" aria-hidden="true"><circle cx="18" cy="18" r="17" fill="#ffffff"/></svg>CVA/DVA (AASB 13 compliant)</li>
        <li class="feature"><svg class="feature-marker" viewBox="0 0 36 36" aria-hidden="true"><circle cx="18" cy="18" r="17" fill="#ffffff"/></svg>Independent valuations</li>
        <li class="feature"><svg class="feature-marker" viewBox="0 0 36 36" aria-hidden="true"><circle cx="18" cy="18" r="17" fill="#ffffff"/></svg>FX, interest rates and commodities</li>
        <li class="feature"><svg class="feature-marker" viewBox="0 0 36 36" aria-hidden="true"><circle cx="18" cy="18" r="17" fill="#ffffff"/></svg>Low monthly subscription</li>
      </ul>
    </section>
    <footer class="brand-row">
      <div class="brand brand--partner">Wren’s Ledger</div>
      <div class="brand brand--product"><svg class="brand-dot" viewBox="0 0 46 46" aria-hidden="true"><circle cx="23" cy="23" r="23" fill="#1b75ba"/></svg>Fenlaris</div>
    </footer>
  </main>
</body>
</html>
```